Veldmark Supplies Business Card

Professional business card that stand out to our potential customers. Front and back with clean modern design

Industry/Entity Type

Oil and gas

Contact Information for Business Card

Name, address, website , office phone and cell number

Requirements
Must have
• Editable files for each employee

```html
<!DOCTYPE html>
<html lang="en">
<head>
<meta charset="utf-8">
<title>Veldmark Supplies Business Card</title>
<link href="https://fonts.googleapis.com/css2?family=Montserrat:wght@500;600;800&display=swap" rel="stylesheet">
<style>
  :root {
    --brand-blue: #0eb0d3;
    --brand-red: #ec2227;
    --ink: #1b1b1b;
    --paper: #ffffff;
    --backdrop: #383838;
  }
  * { box-sizing: border-box; margin: 0; padding: 0; }
  html, body { width: 1200px; height: 689px; overflow: hidden; }
  body {
    background: var(--backdrop);
    font-family: "Montserrat", Arial, sans-serif;
    position: relative;
  }
  .card {
    position: absolute;
    top: 190px;
    width: 540px;
    height: 309px;
    overflow: hidden;
    box-shadow: 0 14px 30px rgba(0,0,0,0.45);
  }
  .card--front { left: 40px; background: var(--brand-blue); }
  .card--back { left: 620px; background: var(--paper); }

  .front-name {
    position: absolute;
    left: 0; right: 0; top: 118px;
    display: flex; align-items: center; justify-content: center; gap: 14px;
  }
  .front-name__mark { width: 30px; height: 30px; background: var(--brand-red); }
  .front-name__text {
    font-weight: 800; font-size: 34px; letter-spacing: 1px;
    color: var(--paper); text-transform: uppercase;
  }

  .back-name {
    position: absolute; left: 26px; top: 128px; width: 200px;
    display: flex; align-items: center; gap: 10px;
  }
  .back-name__mark { width: 18px; height: 18px; background: var(--brand-red); flex: none; }
  .back-name__text {
    font-weight: 800; font-size: 17px; line-height: 1.15;
    color: var(--brand-red); text-transform: uppercase;
  }

  .dividers { position: absolute; left: 232px; top: 40px; }

  .contact { position: absolute; left: 262px; top: 30px; color: var(--ink); }
  .contact__name {
    font-weight: 800; font-size: 19px; color: var(--brand-red);
    text-transform: uppercase; letter-spacing: 0.5px;
  }
  .contact__role { font-weight: 500; font-size: 11px; margin-bottom: 10px; }
  .contact__address { font-weight: 500; font-size: 11px; line-height: 1.35; margin-bottom: 8px; }
  .contact__list { list-style: none; }
  .contact__item {
    display: flex; align-items: center; gap: 8px;
    font-weight: 500; font-size: 11px; line-height: 1; margin-bottom: 5px;
  }
  .contact__icon {
    width: 15px; height: 15px; background: var(--brand-red);
    display: flex; align-items: center; justify-content: center; flex: none;
  }
  .contact__accent { color: var(--brand-red); }

  .swoosh { position: absolute; left: 0; bottom: 0; }
</style>
</head>
<body>
  <section class="card card--front" aria-label="Card front">
    <div class="front-name">
      <span class="front-name__mark"></span>
      <span class="front-name__text">Veldmark Supplies</span>
    </div>
  </section>

  <section class="card card--back" aria-label="Card back">
    <div class="back-name">
      <span class="back-name__mark"></span>
      <span class="back-name__text">Veldmark Supplies</span>
    </div>

    <svg class="dividers" width="24" height="150" viewBox="0 0 24 150" aria-hidden="true">
      <line x1="4" y1="0" x2="4" y2="150" stroke="var(--brand-blue)" stroke-width="1.2"/>
      <line x1="12" y1="15" x2="12" y2="135" stroke="var(--brand-red)" stroke-width="1.2"/>
      <line x1="20" y1="5" x2="20" y2="125" stroke="var(--brand-red)" stroke-width="1.2"/>
    </svg>

    <div class="contact">
      <p class="contact__name">Dane Corliss</p>
      <p class="contact__role">President</p>
      <p class="contact__address">482 Harlow Ave, Ste<br>210, Ardent, TX 75390</p>
      <ul class="contact__list">
        <li class="contact__item">
          <span class="contact__icon"><svg width="9" height="9" viewBox="0 0 10 10"><path d="M2 1l2 0 1 2-1 1c.5 1 1 1.5 2 2l1-1 2 1v2c-4 0-7-3-7-7z" fill="#fff"/></svg></span>
          555-214-3071
        </li>
        <li class="contact__item">
          <span class="contact__icon"><svg width="9" height="9" viewBox="0 0 10 10"><rect x="2.5" y="0.5" width="5" height="9" rx="1" fill="none" stroke="#fff"/><circle cx="5" cy="8" r="0.6" fill="#fff"/></svg></span>
          555-014-8822
        </li>
        <li class="contact__item">
          <span class="contact__icon"><svg width="10" height="8" viewBox="0 0 10 8"><rect x="0.5" y="0.5" width="9" height="7" fill="none" stroke="#fff"/><path d="M0.5 0.5l4.5 4 4.5-4" fill="none" stroke="#fff"/></svg></span>
          info@veldmark-mail.com
        </li>
        <li class="contact__item">
          <span class="contact__icon"><svg width="9" height="9" viewBox="0 0 10 10"><circle cx="5" cy="5" r="4.3" fill="none" stroke="#fff"/><path d="M0.7 5h8.6M5 0.7c-2 2.5-2 6 0 8.6M5 0.7c2 2.5 2 6 0 8.6" fill="none" stroke="#fff" stroke-width="0.8"/></svg></span>
          www.<span class="contact__accent">veldmark-supplies</span>.com
        </li>
      </ul>
    </div>

    <svg class="swoosh" width="540" height="130" viewBox="0 0 540 130" aria-hidden="true">
      <path d="M0 130 L0 100 C150 110 320 80 540 10 L540 130 Z" fill="var(--brand-red)"/>
      <path d="M0 130 L0 114 C160 122 330 94 540 28 L540 130 Z" fill="var(--paper)"/>
      <path d="M0 130 L0 120 C170 126 340 100 540 36 L540 130 Z" fill="var(--brand-blue)"/>
    </svg>
  </section>
</body>
</html>
```